Harrow Grading LLC business card design

Excavation company business cards

Contact Information for Business Card

Harrow Grading LLC cell phone 208-417-6290 office phone 208-319-4856 harrowgradingllc@maplecove.com Driveways, site prep, retaining walls, septic systems, rock delivery

Colors

Designer to choose colors to be used in the design.

```html
<!DOCTYPE html>
<html lang="en">
<head>
<meta charset="utf-8">
<title>Harrow Grading LLC — Business Card</title>
<link href="https://fonts.googleapis.com/css2?family=Montserrat:wght@800&family=Arimo:wght@400;700&display=swap" rel="stylesheet">
<style>
  :root {
    --orange: #e86b1f;
    --orange-deep: #d95f17;
    --gray: #6b6b6b;
    --gray-mid: #7a7a7a;
    --ink: #3a3a3a;
    --white: #ffffff;
    --backdrop: #c4c4c4;
  }
  * { box-sizing: border-box; margin: 0; padding: 0; }
  html, body { width: 1200px; height: 800px; overflow: hidden; }
  body {
    background: var(--backdrop);
    font-family: "Arimo", Arial, sans-serif;
    position: relative;
  }
  .card {
    position: absolute;
    width: 560px;
    height: 320px;
    overflow: hidden;
    box-shadow: 0 10px 30px rgba(0,0,0,0.25);
  }
  /* Front side */
  .card-front { left: 30px; top: 80px; background: var(--white); }
  .front-art {
    position: absolute; right: 0; top: 0; width: 230px; height: 100%;
    background: linear-gradient(135deg, var(--gray-mid) 0%, var(--gray-mid) 30%, var(--orange) 31%, var(--orange) 100%);
  }
  .front-info { position: absolute; left: 40px; top: 40px; width: 290px; }
  .wordmark {
    display: flex; align-items: center; gap: 10px;
    font-family: "Montserrat", sans-serif; font-weight: 800;
    font-size: 24px; color: var(--orange); text-transform: uppercase;
    letter-spacing: 0.5px;
  }
  .wordmark-square { width: 16px; height: 16px; background: var(--orange); flex: none; }
  .person-name {
    margin-top: 46px;
    font-family: "Montserrat", sans-serif; font-weight: 800;
    font-size: 24px; color: var(--orange); letter-spacing: 0.5px;
  }
  .person-title { font-size: 16px; color: var(--ink); margin-top: 2px; }
  .rule { width: 120px; height: 2px; background: var(--orange); margin: 12px 0 12px; }
  .contact-list { list-style: none; }
  .contact-list li {
    display: flex; align-items: center; gap: 10px;
    font-size: 16px; color: var(--ink); line-height: 26px;
  }
  .contact-list svg { width: 16px; height: 16px; flex: none; }

  /* Back side */
  .card-back { left: 610px; top: 400px; background: var(--orange); }
  .back-art {
    position: absolute; right: 20px; top: 20px; width: 200px; height: 200px;
    background: radial-gradient(circle, rgba(217,95,23,0.8) 0%, rgba(232,107,31,0) 70%);
  }
  .back-wordmark {
    position: absolute; left: 0; right: 0; top: 100px; text-align: center;
    font-family: "Montserrat", sans-serif; font-weight: 800;
    font-size: 38px; color: var(--white); text-transform: uppercase;
  }
  .service-band {
    position: absolute; left: 0; right: 0; bottom: 22px; height: 44px;
    background: var(--gray);
    display: flex; align-items: center; justify-content: center; gap: 10px;
    color: var(--white); font-size: 16px;
  }
  .service-band .dot { width: 6px; height: 6px; border-radius: 50%; background: var(--white); }
</style>
</head>
<body>

  <section class="card card-front" aria-label="Business card front">
    <div class="front-art" role="img" aria-label="Large excavator bucket illustration in orange on gray"></div>
    <div class="front-info">
      <div class="wordmark"><span class="wordmark-square"></span>Harrow Grading LLC</div>
      <h1 class="person-name">MARCUS HALE</h1>
      <p class="person-title">Managing Director</p>
      <div class="rule"></div>
      <ul class="contact-list">
        <li>
          <svg viewBox="0 0 16 16"><rect x="4" y="1" width="8" height="14" rx="1.5" fill="none" stroke="#e86b1f" stroke-width="1.6"/><circle cx="8" cy="12.5" r="0.9" fill="#e86b1f"/></svg>
          208-417-6290
        </li>
        <li>
          <svg viewBox="0 0 16 16"><path d="M3 2 L6 2 L7 5 L5 6.5 C6 8.5 7.5 10 9.5 11 L11 9 L14 10 L14 13 C14 14 13 14.5 12 14.5 C7 14 2 9 1.5 4 C1.5 3 2 2 3 2Z" fill="#e86b1f"/></svg>
          208-319-4856
        </li>
        <li>
          <svg viewBox="0 0 16 16"><rect x="1" y="3" width="14" height="10" fill="#e86b1f"/><path d="M1 3 L8 9 L15 3" fill="none" stroke="#fff" stroke-width="1.2"/></svg>
          harrowgradingllc@maplecove.com
        </li>
      </ul>
    </div>
  </section>

  <section class="card card-back" aria-label="Business card back">
    <div class="back-art" role="img" aria-label="Faint excavator bucket decoration"></div>
    <div class="back-wordmark">Harrow Grading LLC</div>
    <div class="service-band">
      <span>Driveways</span><span class="dot"></span>
      <span>Site prep</span><span class="dot"></span>
      <span>Retaining walls</span><span class="dot"></span>
      <span>Septic systems</span><span class="dot"></span>
      <span>Rock delivery</span>
    </div>
  </section>

</body>
</html>
```